Bry7Legal Letterhead

Need a new letterhead for my law firm.
IDENTIFYING INFORMATION BELOW:
Anselmo R Quintara III
Attorney at Law
Address: 2847 Larkspur Blvd, Ste 300, Dallas, TX 75204
Phone: 877-482-6017
Fax: 469-738-1452
Email: bry@bry7legal.example
Website: www.bry7legal.example

Colors
0054AA
0677BA
7BADD7
CADEEF
E8F1F8

Requirements
Must have
• Logo needs to be on the letterhead, along with identifying information which is included in the project description.

```html
<!DOCTYPE html>
<html lang="en">
<head>
<meta charset="utf-8">
<title>Bry7Legal Letterhead</title>
<link href="https://fonts.googleapis.com/css2?family=Inter:wght@400;500&family=Arimo:wght@400&display=swap" rel="stylesheet">
<style>
  :root {
    --backdrop: #e6e8eb;
    --ink: #111111;
    --body-ink: #555555;
    --accent: #0677BA;
    --accent-bright: #1a90d0;
    --rule: #333333;
    --sign-area: #E8F1F8;
  }
  * { margin: 0; padding: 0; box-sizing: border-box; }
  html, body {
    width: 1039px; height: 1200px; overflow: hidden;
    background: var(--backdrop);
  }
  .letter {
    position: absolute; left: 104px; top: 16px;
    width: 830px; height: 1168px;
    background: linear-gradient(135deg, #ffffff 0%, #ededed 55%, #dcdcdc 100%);
    box-shadow: 0 2px 6px rgba(0,0,0,0.18);
  }
  .brand {
    position: absolute; top: 80px; left: 0; width: 100%;
    display: flex; align-items: center; justify-content: center; gap: 10px;
  }
  .brand-mark {
    width: 14px; height: 14px; background: var(--accent);
  }
  .brand-name {
    font-family: "Inter", sans-serif; font-weight: 500; font-size: 30px;
    color: var(--ink); line-height: 1;
  }
  .content {
    position: absolute; left: 62px; top: 390px; width: 701px;
    font-family: "Arimo", sans-serif; color: var(--body-ink);
  }
  .salutation { font-size: 17px; margin-bottom: 20px; }
  .content p.body {
    font-size: 12.6px; line-height: 19.6px; text-align: justify;
    margin-bottom: 19.6px; hyphens: auto;
  }
  .closing { font-size: 12.6px; }
  .signature {
    position: absolute; left: 62px; top: 790px;
    width: 106px; height: 44px; background: var(--sign-area);
  }
  .footer {
    position: absolute; left: 0; top: 1066px; width: 100%;
    text-align: center; font-family: "Inter", sans-serif; color: var(--ink);
  }
  .attorney-name {
    font-weight: 500; font-size: 18px; color: var(--accent-bright);
  }
  .title-row {
    display: flex; align-items: center; justify-content: center; gap: 4px;
  }
  .title-row .rule { width: 156px; height: 1px; background: var(--rule); }
  .title-row .title { font-size: 11px; }
  .contact { margin-top: 12px; font-size: 12px; line-height: 18px; }
</style>
</head>
<body>
  <div class="letter">
    <header class="brand">
      <span class="brand-mark"></span>
      <span class="brand-name">Bry7Legal</span>
    </header>

    <main class="content">
      <p class="salutation">Dear Mr. Smith,</p>
      <p class="body">Lorem ipsum dolor sit amet, consectetur adipiscing elit. Donec orci purus, luctus vitae dignissim eu, iaculis sed purus. Vivamus faucibus, ipsum nec aliquet viverra, leo mauris condimentum ligula, sit amet sagittis enim ligula quis arcu. Nam egestas tortor id nisi porttitor mattis. In tortor ante, ultricies in suscipit a, tempus non massa. Vivamus et auctor mi. Fusce vel massa nulla. Phasellus nec eros mauris, et scelerisque orci.</p>
      <p class="body">Donec malesuada orci vitae nulla accumsan porta a id massa. Quisque accumsan iaculis magna sit amet fringilla. Maecenas consequat, magna eget tincidunt semper, odio nibh rutrum mi, id feugiat ante nisi eu risus. Vestibulum nunc orci, rhoncus a placerat in, ultricies in mi. Cras mattis varius eros, vel fringilla nisi suscipit eget. Quisque scelerisque sagittis nulla at porttitor.</p>
      <p class="body">Sed id augue vitae urna euismod commodo aliquet a quam. Pellentesque arcu velit, cursus et malesuada ut, consequat et diam. Nullam erat sem, rhoncus id ullamcorper vitae, rhoncus et arcu. In ultricies ultricies nulla, ut rutrum nisi iaculis at. Donec eu magna a metus ornare faucibus. Fusce aliquet faucibus ultricies. Morbi semper, est id tincidunt gravida, sem arcu adipiscing lacus, ac bibendum nulla leo eu purus. Quisque nec diam sed risus consectetur a ccumsan quis quis nibh. Vestibulum id purus lorem.</p>
      <p class="closing">Sincerely,</p>
    </main>

    <div class="signature" role="img" aria-label="Handwritten signature of the attorney"></div>

    <footer class="footer">
      <div class="attorney-name">Anselmo R Quintara III</div>
      <div class="title-row">
        <span class="rule"></span>
        <span class="title">Attorney at Law</span>
        <span class="rule"></span>
      </div>
      <div class="contact">
        P. 877-482-6017 F. 469-738-1452 E. bry@bry7legal.example W. bry7legal.example<br>
        2847 Larkspur Blvd, Ste 300, Dallas, TX 75204
      </div>
    </footer>
  </div>
</body>
</html>
```